Multiple website banners for a shopify theme

I need custom designed banners for a destributor webpage.

We will be selling products in our local store from a supplier https://glimmorabath.co.uk (you can get the ideas from their site).

We need custom desings:
- 2-3x 1920x745
- 1x 960x960
- 2x 480x480
- 1x 960*480
All of theme need to nicely fit together as shown in the uploaded layout screenshot (website_banner_layout).
In Google drive link there are products pictures which must be used in the banners.

https://files.quorvane.net/share/folders/7TkpWq2LmXe9VbNa4cHsYdRuF3jGz8Qo?mode=view

Kids, Cosmetics market

Cosmetics

• Playful elements

```html
<!DOCTYPE html>
<html lang="en">
<head>
<meta charset="utf-8">
<title>Glimmora Bath – Banner Set</title>
<link rel="stylesheet" href="https://fonts.googleapis.com/css2?family=League+Spartan:wght@700;800&family=Poppins:wght@500;600&display=swap">
<style>
  :root {
    --board: #d2d2d2;
    --white: #ffffff;
    --pink-hot: #ee3b7b;
    --pink-mid: #f4669c;
    --pink-soft: #f9a6c6;
    --blue-deep: #5a7be0;
    --blue-soft: #a9bff2;
    --navy: #1f2f8f;
    --green: #5a9e7c;
    --crimson: #d91e5b;
    --label: #222222;
    --shadow: 0 6px 14px rgba(0,0,0,.22);
  }
  * { box-sizing: border-box; margin: 0; padding: 0; }
  html, body { width: 1200px; height: 805px; overflow: hidden; background: var(--board); }
  .board { position: relative; width: 1200px; height: 805px; }

  .banner { position: absolute; overflow: hidden; box-shadow: var(--shadow); background: var(--white); font-family: "League Spartan", "Poppins", sans-serif; }
  .banner .backdrop { position: absolute; left: 0; top: 0; width: 100%; }
  .size-label { position: absolute; font-family: "Poppins", sans-serif; font-weight: 500; font-size: 22px; color: var(--label); transform: translateX(-50%); white-space: nowrap; letter-spacing: .5px; }

  .brand { position: absolute; display: flex; align-items: center; gap: 6px; color: var(--white); font-weight: 800; letter-spacing: .5px; z-index: 2; }
  .brand .dot { border-radius: 50%; background: var(--white); flex: none; }

  .headline { position: absolute; color: var(--white); font-weight: 800; text-transform: uppercase; line-height: 1; white-space: nowrap; z-index: 2; }
  .headline.navy { color: var(--navy); }

  .product { position: absolute; border-radius: 18px; z-index: 1; }
  .price { position: absolute; border-radius: 50%; background: var(--white); border: 2px dashed currentColor; display: flex; align-items: center; justify-content: center; font-family: "League Spartan", sans-serif; font-weight: 700; z-index: 3; }
  .cta { position: absolute; display: flex; align-items: center; justify-content: center; color: var(--white); font-family: "Poppins", sans-serif; font-weight: 600; border-radius: 999px; text-transform: uppercase; z-index: 3; }

  /* 960 x 960 */
  .b-square-lg { left: 58px; top: 124px; width: 518px; height: 518px; }
  .b-square-lg .backdrop { height: 376px; background: linear-gradient(115deg, var(--pink-hot) 0%, var(--pink-mid) 55%, #f7a3c4 100%); }
  .b-square-lg .brand { left: 206px; top: 40px; font-size: 26px; }
  .b-square-lg .brand .dot { width: 34px; height: 34px; }
  .b-square-lg .headline { left: 0; width: 100%; top: 132px; text-align: center; font-size: 39px; line-height: 38px; }
  .b-square-lg .product { left: 130px; top: 228px; width: 296px; height: 224px; background: radial-gradient(ellipse at 45% 50%, #f2c6d4 0%, #d9b98a 45%, #f7d6e1 80%, rgba(255,255,255,0) 100%); }
  .b-square-lg .price { left: 321px; top: 218px; width: 72px; height: 72px; color: var(--crimson); font-size: 22px; }
  .b-square-lg .cta { left: 186px; top: 463px; width: 144px; height: 30px; background: var(--green); font-size: 17px; border-radius: 8px; }

  /* 480 x 480 duo */
  .b-duo { left: 607px; top: 96px; width: 259px; height: 259px; }
  .b-duo .backdrop, .b-blaster .backdrop { height: 198px; background: linear-gradient(120deg, var(--blue-deep) 0%, var(--blue-soft) 100%); }
  .b-duo .brand { left: 14px; top: 18px; font-size: 12px; gap: 4px; }
  .b-duo .brand .dot, .b-blaster .brand .dot { width: 16px; height: 16px; }
  .b-duo .headline { left: 14px; top: 56px; font-size: 17px; line-height: 19px; }
  .b-duo .product { left: 132px; top: 70px; width: 122px; height: 180px; background: linear-gradient(160deg, #f07aa8 0%, #c88ad8 55%, #f3c2d6 100%); }
  .b-duo .price { left: 69px; top: 144px; width: 44px; height: 44px; color: var(--navy); font-size: 13px; }
  .b-duo .cta { left: 14px; top: 230px; width: 68px; height: 14px; background: var(--navy); font-size: 8px; }

  /* 480 x 480 blaster */
  .b-blaster { left: 883px; top: 96px; width: 259px; height: 259px; }
  .b-blaster .brand { left: 106px; top: 20px; font-size: 12px; gap: 4px; }
  .b-blaster .headline { left: 0; width: 100%; top: 66px; text-align: center; font-size: 22px; line-height: 24px; }
  .b-blaster .product { left: 26px; top: 118px; width: 204px; height: 112px; background: linear-gradient(90deg, #b7dcc6 0%, #f26fb0 40%, #5fb7ec 60%, #f59ac0 100%); border-radius: 56px; }
  .b-blaster .price { left: 203px; top: 192px; width: 40px; height: 40px; color: var(--navy); font-size: 11px; }
  .b-blaster .cta { left: 91px; top: 228px; width: 76px; height: 16px; background: var(--navy); font-size: 8px; }

  /* 960 x 480 */
  .b-wide { left: 614px; top: 410px; width: 518px; height: 259px; }
  .b-wide .backdrop { height: 190px; background: linear-gradient(100deg, var(--pink-hot) 0%, var(--pink-mid) 60%, var(--pink-soft) 100%); }
  .b-wide .halo { position: absolute; left: 286px; top: 10px; width: 240px; height: 240px; border-radius: 50%; background: #f8a9c8; }
  .b-wide .brand { left: 22px; top: 46px; font-size: 21px; }
  .b-wide .brand .dot { width: 30px; height: 30px; }
  .b-wide .headline { left: 25px; top: 112px; font-size: 27px; line-height: 30px; }
  .b-wide .product { left: 318px; top: 18px; width: 190px; height: 160px; background: linear-gradient(150deg, #c9a57a 0%, #e23a7e 50%, #c02d6c 100%); border-radius: 14px; }
  .b-wide .product-soaps { left: 190px; top: 176px; width: 300px; height: 64px; background: linear-gradient(90deg, #f6b24a 0%, #d93a5a 40%, #5f8fe0 65%, #f07aa8 100%); border-radius: 14px; }
  .b-wide .cta { left: 26px; top: 203px; width: 118px; height: 24px; background: var(--crimson); font-size: 13px; }
</style>
</head>
<body>
<main class="board">

  <section class="banner b-square-lg" aria-label="Petal Tales Candle banner">
    <div class="backdrop"></div>
    <div class="brand"><span class="dot"></span>GLIMMORA</div>
    <h2 class="headline">Petal Tales<br>Candle</h2>
    <div class="product" role="img" aria-label="Product photo: rose scented candle tin with lid and pink roses"></div>
    <div class="price">£9.25</div>
    <a class="cta">Shop Now</a>
  </section>
  <p class="size-label" style="left:317px; top:668px;">960 x 960</p>

  <section class="banner b-duo" aria-label="Glow Up duo banner">
    <div class="backdrop"></div>
    <div class="brand"><span class="dot"></span>GLIMMORA</div>
    <h2 class="headline navy">21 &amp; Fabulous<br>Glow Up<br>Bath Fizz<br>&amp; Candle<br>Duo</h2>
    <div class="product" role="img" aria-label="Product photo: birthday bath fizz and candle duo with sprinkles and fruit"></div>
    <div class="price">£12.99</div>
    <a class="cta">Shop Now</a>
  </section>
  <p class="size-label" style="left:737px; top:368px;">480 x 480</p>

  <section class="banner b-blaster" aria-label="Fizz blaster banner">
    <div class="backdrop"></div>
    <div class="brand"><span class="dot"></span>GLIMMORA</div>
    <h2 class="headline navy">Born to Sparkle<br>Fizz Blaster</h2>
    <div class="product" role="img" aria-label="Product photo: three colourful bath blasters with toppers"></div>
    <div class="price">£3.75</div>
    <a class="cta">Shop Now</a>
  </section>
  <p class="size-label" style="left:1012px; top:368px;">480 x 480</p>

  <section class="banner b-wide" aria-label="Mystery soap slices banner">
    <div class="backdrop"></div>
    <div class="halo"></div>
    <div class="product" role="img" aria-label="Product photo: open gift box filled with colourful soap slices"></div>
    <div class="product product-soaps" role="img" aria-label="Product photo: soap slices and amber soap pieces in front of the box"></div>
    <div class="brand"><span class="dot"></span>GLIMMORA</div>
    <h2 class="headline">5 Mystery Soap<br>Slices for £10</h2>
    <a class="cta">Shop Now</a>
  </section>
  <p class="size-label" style="left:872px; top:684px;">960 x 480</p>

</main>
</body>
</html>
```